Website Landing Page for Medical Recruitment

Looking for a landing page to add to our existing website. The objective of the page is to recruit new clinical staff for various departments within Pinecrest Medical Center (non-profit hospital in the Richmond, TX area).

We would like the page to be modern, professional, and non-cluttered. Please include call-to-actions and include a button that will navigate to the page where candidates can submit their applications (this page already exists).

Target Market(s)

25-35-year-olds who live in the Houston and Richmond area with medical experience.

Industry/Entity Type

Medical/Health

Font styles to use
Sans Serif

Colors
0054AA
0677BA
7BADD7
CADEEF
E8F1F8

Requirements
Must have
• A "call to action"; a button that navigates to pinecrestmedhub.example/careers

```html
<!DOCTYPE html>
<html lang="en">
<head>
<meta charset="utf-8">
<title>Pinecrest Medical Center – Careers</title>
<link rel="stylesheet" href="https://fonts.googleapis.com/css2?family=Cinzel:wght@500;600&family=Lato:wght@400;700&family=Roboto:wght@400;500;700&display=swap">
<style>
:root{
  --blue-deep:#0054aa;
  --blue:#0677ba;
  --blue-brand:#1a6aa5;
  --blue-soft:#7badd7;
  --blue-pale:#cadeef;
  --blue-mist:#e8f1f8;
  --ink:#222;
  --text:#555;
  --white:#fff;
  --grey:#dcdcdc;
}
*{box-sizing:border-box;margin:0;padding:0}
html,body{width:1200px;height:3600px;overflow:hidden}
body{position:relative;background:var(--white);font-family:'Roboto',sans-serif;color:var(--ink)}
.abs{position:absolute}
.topline{left:0;top:0;width:1200px;height:4px;background:var(--blue-brand)}
.brand{left:110px;top:22px;display:flex;align-items:center;gap:12px}
.brand-dot{width:40px;height:40px;border-radius:50%;background:var(--blue-brand)}
.brand-name{font-family:'Roboto',sans-serif;font-weight:500;font-size:24px;color:var(--blue-brand);line-height:1}
.nav{left:463px;top:40px;display:flex;gap:25px;font-size:14px;font-weight:700;color:#333}
.nav a{color:inherit;text-decoration:none;padding-bottom:6px}
.nav a.active{color:var(--blue-brand);border-bottom:2px solid var(--blue-brand)}
.btn{display:inline-flex;align-items:center;justify-content:center;border-radius:24px;font-weight:700;font-size:14px;text-decoration:none;font-family:'Roboto',sans-serif}
.btn-blue{background:var(--blue-brand);color:var(--white)}
.btn-white{background:var(--white);color:var(--blue-brand)}
.btn .arr{display:inline-block;width:13px;height:13px;border-radius:50%;background:currentColor;margin-left:5px;position:relative}
.btn .arr::after{content:"";position:absolute;left:3px;top:3.5px;border:3px solid transparent;border-left:5px solid var(--blue-brand)}
.btn-blue .arr::after{border-left-color:var(--blue-brand)}
.btn-white .arr{background:var(--blue-brand)}
.btn-white .arr::after{border-left-color:var(--white)}
.btn-blue .arr{background:var(--white)}
.careers-btn{left:987px;top:29px;width:102px;height:42px}
.hero-photo{left:0;top:94px;width:1200px;height:690px;background:linear-gradient(100deg,#e9eef3 0%,#d6e0ea 45%,#8fb3d8 62%,#c7d3df 80%,#eef1f4 100%)}
.hero-circle{left:148px;top:192px;width:416px;height:416px;border-radius:50%;background:var(--blue-brand);text-align:center;color:var(--white)}
.hero-circle h1{font-family:'Cinzel',serif;font-weight:600;font-size:56px;line-height:69px;margin-top:82px}
.hero-circle .btn{width:160px;height:40px;margin-top:10px}
.arrow{width:52px;height:52px;border-radius:50%;background:#555;top:362px;display:flex;align-items:center;justify-content:center}
.section-mark{width:34px;height:34px;border-radius:50%;border:3px solid var(--blue-brand);left:583px}
.section-title{left:0;width:1200px;text-align:center;font-family:'Cinzel',serif;font-weight:600;font-size:49px;color:var(--blue-brand);letter-spacing:1px}
.about-text{left:150px;width:900px;text-align:center;font-family:'Lato',sans-serif;font-size:13.5px;line-height:26px;color:var(--text)}
.about-text p+p{margin-top:25px}
.band{left:0;top:1610px;width:1200px;height:560px;background:linear-gradient(180deg,#1b6ba7,#155d96)}
.card-photo{width:226px;height:266px;background:linear-gradient(160deg,var(--blue-pale),var(--blue-soft) 60%,#5a8fc0)}
.r-br{border-bottom-right-radius:60px}
.r-tl{border-top-left-radius:60px}
.card-label{width:226px;text-align:center;color:var(--white);font-family:'Lato',sans-serif;font-weight:700;font-size:19px;line-height:26px}
.careers-text{left:0;width:1200px;text-align:center;color:var(--white);font-family:'Lato',sans-serif;font-weight:700;font-size:14px;line-height:26px}
.blog-card{width:312px;height:406px;text-align:center;background:var(--white)}
.blog-card.raised{box-shadow:0 2px 10px rgba(0,0,0,.15)}
.blog-photo{margin:7px auto 0;width:303px;height:193px;background:linear-gradient(135deg,var(--blue-mist),var(--blue-soft) 55%,#3c78b0)}
.blog-card h3{font-weight:400;font-size:22px;margin-top:22px;color:#222}
.blog-card .rule{width:38px;height:2px;background:#5fa9a6;margin:12px auto 14px}
.blog-card p{font-size:14px;line-height:26px;color:var(--text);padding:0 26px}
.blog-card a{display:inline-block;margin-top:14px;font-size:15px;color:var(--blue-brand);text-decoration:underline}
.footer-band{left:0;top:2860px;width:1200px;height:520px;background:linear-gradient(160deg,#1c6aa6,#0f5a94)}
.fold{top:3385px;width:0;height:0;border-top:120px solid var(--grey)}
.panel{left:112px;top:3155px;width:976px;height:356px;background:var(--white)}
.contact-item{left:178px;display:flex;gap:16px}
.ci-icon{width:58px;height:58px;border-radius:50%;background:var(--blue-brand);display:flex;align-items:center;justify-content:center;flex:none}
.ci-body{padding-top:4px;font-size:14px;line-height:25px;color:#333}
.ci-body strong{display:block;font-size:16px;color:#111}
.field{width:236px;border-bottom:1px solid #ddd;font-size:14px;color:#999;padding-bottom:12px}
.field.wide{width:500px}
.submit{left:520px;top:3414px;width:128px;height:40px;background:var(--blue-brand);color:var(--white);font-weight:700;font-size:14px;display:flex;align-items:center;justify-content:center}
.copyright{left:0;top:3528px;width:1200px;text-align:center;font-size:13px;color:#333}
</style>
</head>
<body>

<div class="abs topline"></div>
<div class="abs brand"><span class="brand-dot"></span><span class="brand-name">Pinecrest Medical Center</span></div>
<nav class="abs nav">
  <a class="active" href="#">HOME</a><a href="#">ABOUT US</a><a href="#">SERVICES</a><a href="#">BLOG</a><a href="#">REVIEWS</a><a href="#">CONTACT US</a>
</nav>
<a class="abs btn btn-blue careers-btn" href="https://pinecrestmedhub.example/careers">CAREERS</a>

<div class="abs hero-photo" role="img" aria-label="Smiling nurse in blue scrubs standing with arms crossed in a bright hospital room"></div>
<svg class="abs" style="left:0;top:680px" width="1200" height="110" viewBox="0 0 1200 110">
  <path d="M0 60 C250 110 520 100 760 60 C950 30 1100 30 1200 40 L1200 110 L0 110Z" fill="#fff"/>
  <path d="M150 88 C400 90 650 40 850 25 C950 18 1020 22 1050 24 C900 30 700 70 500 92 C380 100 260 98 150 88Z" fill="#1a6aa5"/>
</svg>
<div class="abs hero-circle">
  <h1>GIVE BACK<br>TO<br>PINECREST</h1>
  <a class="btn btn-white" href="https://pinecrestmedhub.example/careers">GET STARTED<span class="arr"></span></a>
</div>
<div class="abs arrow" style="left:30px"><svg width="14" height="14" viewBox="0 0 14 14"><path d="M9 2 L4 7 L9 12" stroke="#fff" stroke-width="2" fill="none"/></svg></div>
<div class="abs arrow" style="left:1118px"><svg width="14" height="14" viewBox="0 0 14 14"><path d="M5 2 L10 7 L5 12" stroke="#fff" stroke-width="2" fill="none"/></svg></div>

<div class="abs section-mark" style="top:826px"></div>
<h2 class="abs section-title" style="top:870px">ABOUT PINECREST</h2>
<div class="abs about-text" style="top:936px">
  <p>On July 23, 1947, at the invitation of Mr. and Mrs. H.L. Marsh, the following people met at the H.L. Marsh farm for the purpose of organizing and establishing a hospital in Cedar Bend County. Each of these individuals was asked to associate themselves with the hospital and each accepted: H.L. Marsh, Clara B. Marsh, R.T. Hollis, B.J. Carver, L.M. Oberlin, D.F. Tanner, Preston Vale, S.K. Whitlow, E.G. Lyle, N.O. Pruitt, and Samuel T. Rowe, Jr.</p>
  <p>These public spirited citizens reviewed findings on the health needs of Cedar Bend County and concluded that a real need did exist in this area for a hospital. The T.W.B. Ashford home in Richmond, consisting of approximately twenty-five acres, was donated by Mr. and Mrs. H.L. Marsh as the site for the hospital.</p>
</div>
<a class="abs btn btn-blue" style="left:519px;top:1164px;width:162px;height:42px" href="#">LEARN MORE<span class="arr"></span></a>

<div class="abs section-mark" style="top:1312px"></div>
<h2 class="abs section-title" style="top:1356px">POSITIONS WE HAVE AVAILABLE</h2>

<div class="abs band"></div>
<svg class="abs" style="left:0;top:2080px" width="1200" height="100" viewBox="0 0 1200 100">
  <path d="M0 60 C250 110 520 100 760 60 C950 30 1100 30 1200 40 L1200 100 L0 100Z" fill="#fff"/>
  <path d="M150 90 C400 92 650 42 850 27 C950 20 1020 24 1050 26 C900 32 700 72 500 94 C380 100 260 100 150 90Z" fill="#1a6aa5"/>
</svg>

<div class="abs card-photo r-br" style="left:8px;top:1443px" role="img" aria-label="Nurse helping an elderly patient walk"></div>
<div class="abs card-label" style="left:8px;top:1722px">Certified Nurses<br>Assistants</div>
<div class="abs card-photo r-tl" style="left:248px;top:1486px" role="img" aria-label="Emergency room technician in surgical gear"></div>
<div class="abs card-label" style="left:248px;top:1765px">Emergency Room<br>Techs</div>
<div class="abs card-photo r-br" style="left:488px;top:1443px" role="img" aria-label="Vocational nurse caring for an older patient"></div>
<div class="abs card-label" style="left:488px;top:1722px">Licensed Vocational<br>Nurses</div>
<div class="abs card-photo r-tl r-br" style="left:728px;top:1486px" role="img" aria-label="Registered nurse on the phone at a desk"></div>
<div class="abs card-label" style="left:728px;top:1765px">Registered Nurses</div>
<div class="abs card-photo r-br" style="left:968px;top:1443px" role="img" aria-label="Unit secretaries reviewing a tablet"></div>
<div class="abs card-label" style="left:968px;top:1722px">Unit Secretaries</div>

<h2 class="abs section-title" style="top:1856px;color:var(--white)">OUR CAREERS</h2>
<div class="abs careers-text" style="top:1932px">Join our team of talented health care professionals as we serve our community with our values of compassion,<br>integrity, ownership and excellence.</div>
<a class="abs btn btn-white" style="left:519px;top:2010px;width:162px;height:42px" href="https://pinecrestmedhub.example/careers">LEARN MORE<span class="arr"></span></a>

<div class="abs section-mark" style="top:2220px"></div>
<h2 class="abs section-title" style="top:2264px">LATEST BLOG</h2>

<article class="abs blog-card" style="left:112px;top:2353px">
  <div class="blog-photo" role="img" aria-label="Staff moving a bed down a hospital corridor"></div>
  <h3>Duis aute irure dolor</h3><div class="rule"></div>
  <p>Lorem ipsum dolor sit amet, conse ctetur adipiscing elit, sed do eiusmod tempor incididunt ut labore</p>
  <a href="#">LEARN MORE</a>
</article>
<article class="abs blog-card raised" style="left:444px;top:2353px">
  <div class="blog-photo" role="img" aria-label="Two nurses smiling while looking at a laptop"></div>
  <h3>Duis aute irure dolor</h3><div class="rule"></div>
  <p>Lorem ipsum dolor sit amet, conse ctetur adipiscing elit, sed do eiusmod tempor incididunt ut labore</p>
  <a href="#">LEARN MORE</a>
</article>
<article class="abs blog-card" style="left:777px;top:2353px">
  <div class="blog-photo" role="img" aria-label="Nurse working at a computer"></div>
  <h3>Duis aute irure dolor</h3><div class="rule"></div>
  <p>Lorem ipsum dolor sit amet, conse ctetur adipiscing elit, sed do eiusmod tempor incididunt ut labore</p>
  <a href="#">LEARN MORE</a>
</article>

<div class="abs footer-band"></div>
<svg class="abs" style="left:0;top:2850px" width="1200" height="110" viewBox="0 0 1200 110">
  <path d="M0 0 L1200 0 L1200 20 C1000 10 800 30 600 60 C380 95 150 95 0 50Z" fill="#fff"/>
  <path d="M150 80 C400 90 650 40 850 25 C950 18 1020 20 1050 22 C900 28 700 66 500 86 C380 96 260 94 150 80Z" fill="#1a6aa5"/>
</svg>
<div class="abs fold" style="left:56px;border-left:56px solid transparent;border-right:0 solid transparent;border-top-width:120px"></div>
<div class="abs fold" style="left:1088px;border-right:56px solid transparent"></div>

<div class="abs section-mark" style="top:3024px;border-color:var(--white)"></div>
<h2 class="abs section-title" style="top:3068px;color:var(--white)">GET IN TOUCH</h2>

<div class="abs panel"></div>
<div class="abs contact-item" style="top:3208px">
  <div class="ci-icon"><svg width="18" height="22" viewBox="0 0 18 22"><path d="M9 1a7 7 0 0 0-7 7c0 5 7 13 7 13s7-8 7-13a7 7 0 0 0-7-7z" fill="#fff"/><circle cx="9" cy="8" r="2.6" fill="#1a6aa5"/></svg></div>
  <div class="ci-body"><strong>Address :</strong>Lorem ipsum dolor sit amet,<br>consectetur adipiscing</div>
</div>
<div class="abs contact-item" style="top:3312px">
  <div class="ci-icon"><svg width="20" height="20" viewBox="0 0 20 20"><path d="M4 2l3 0 2 5-2 1.5c1 2.5 3 4.5 5.5 5.5L14 12l5 2v3c0 1-1 2-2 2C9 19 1 11 1 3c0-1 1-1 3-1z" fill="#fff"/></svg></div>
  <div class="ci-body"><strong>Phone :</strong>+1 888 888 8888</div>
</div>
<div class="abs contact-item" style="top:3404px">
  <div class="ci-icon"><svg width="22" height="16" viewBox="0 0 22 16"><rect x="1" y="1" width="20" height="14" rx="1" fill="#fff"/><path d="M1 2l10 7 10-7" stroke="#1a6aa5" stroke-width="1.8" fill="none"/></svg></div>
  <div class="ci-body"><strong>Email Address :</strong>info@companyname.com</div>
</div>

<div class="abs field" style="left:520px;top:3219px">First name</div>
<div class="abs field" style="left:784px;top:3219px">Last name</div>
<div class="abs field" style="left:520px;top:3288px">Email</div>
<div class="abs field" style="left:784px;top:3288px">Company</div>
<div class="abs field wide" style="left:520px;top:3357px">Subject</div>
<div class="abs submit">SUBMIT NOW</div>

<div class="abs copyright">Copyright &nbsp;© 2022 Company name | Privacy Policy | Terms &amp; Conditions</div>

</body>
</html>
```